Meridale Partners Website

Meridale Partners (MP) provide Analytics & Enterprise Performance Management (EPM) advisory & consultancy services. We are passionate about data and making a difference for our clients by working in partnership with them, helping them on their journey to becoming an Meridale Partner. We deliver insights which give our clients a competitive edge and a much deeper understanding of their organisation.

We need a website which shows who we are, what we do and how we do it.

www.meridale-partners.example is our very basic website at the moment. We want to completely revamp it with a corporate look

```html
<!DOCTYPE html>
<html lang="en">
<head>
<meta charset="utf-8">
<title>Meridale Partners</title>
<link href="https://fonts.googleapis.com/css2?family=Montserrat:wght@600;700;800&family=Lato:wght@400;700&display=swap" rel="stylesheet">
<style>
:root{
  --blue:#2a5570;
  --blue-dark:#1f455c;
  --orange:#e58a45;
  --ink:#111;
  --grey:#555;
  --footer:#0a0a0a;
  --white:#fff;
}
*{box-sizing:border-box;margin:0;padding:0}
html,body{width:1200px;height:3405px;overflow:hidden}
body{position:relative;font-family:'Lato',sans-serif;color:var(--ink);background:var(--white)}
.abs{position:absolute}
.head{font-family:'Montserrat',sans-serif}
/* header */
.topbar{left:0;top:0;width:1200px;height:63px}
.topbar-info{top:18px;left:500px;display:flex;align-items:center;gap:14px;color:#fff;font-family:'Montserrat',sans-serif;font-weight:600;font-size:15px}
.ico{width:32px;height:32px;border-radius:50%;background:#fff;display:inline-flex;align-items:center;justify-content:center}
.soc{width:26px;height:26px;border-radius:50%;background:#fff;display:inline-block}
.brand{left:98px;top:34px;display:flex;align-items:center;gap:14px}
.brand-dot{width:56px;height:56px;border-radius:50%;border:9px solid var(--blue)}
.brand-name{font-family:'Montserrat',sans-serif;font-weight:700;font-size:25px;line-height:29px;color:var(--blue);letter-spacing:.5px;text-transform:uppercase}
.nav{top:94px;left:444px;display:flex;gap:56px;font-family:'Lato',sans-serif;font-size:16px;font-weight:700;color:#222}
.nav .active{color:var(--blue);text-decoration:underline;text-underline-offset:5px}
/* hero */
.hero{left:0;top:141px;width:1200px;height:652px}
.hero-title{left:92px;top:290px;color:#fff;font-family:'Montserrat',sans-serif;font-weight:700;font-size:44px;line-height:56px;text-transform:uppercase}
.hero-text{left:93px;top:399px;width:540px;color:#fff;font-size:15px;line-height:29px}
.btn{display:inline-flex;align-items:center;justify-content:center;font-family:'Montserrat',sans-serif;font-weight:700;font-size:19px;text-transform:uppercase;border-radius:30px 6px 30px 30px;box-shadow:4px 4px 0 rgba(0,0,0,.12)}
.btn-orange{background:var(--orange);color:#fff}
.btn-white{background:#fff;color:var(--blue)}
/* about */
.eyebrow{font-family:'Montserrat',sans-serif;font-weight:700;font-size:16px;letter-spacing:4px;text-transform:uppercase;color:var(--blue)}
.h2{font-family:'Montserrat',sans-serif;font-weight:700;font-size:36px;color:#111}
.body-text{font-size:15px;line-height:29px;color:#333}
/* services */
.card{overflow:hidden}
.card-title{font-family:'Lato',sans-serif;font-weight:700;font-size:24px;color:#fff}
.card-text{font-size:13px;line-height:25px;color:#fff}
/* testimonial */
.quote{font-size:15px;line-height:29px;color:#333;text-align:right}
.dot{width:11px;height:11px;border-radius:50%;background:#bbb;display:inline-block;margin-left:11px}
/* footer */
.foot-h{font-family:'Lato',sans-serif;font-weight:700;font-size:23px;color:#fff}
.foot-list{list-style:none;color:#fff;font-size:15px}
.foot-list li{height:34px;display:flex;align-items:center;gap:14px}
.foot-soc{width:30px;height:30px;border-radius:50%;background:var(--blue);display:inline-block;margin-right:24px}
</style>
</head>
<body>

<!-- header -->
<svg class="abs topbar" width="1200" height="63" viewBox="0 0 1200 63">
  <polygon points="455,0 1200,0 1200,63 500,63" fill="var(--blue)"/>
  <polygon points="423,0 440,0 486,63 470,63" fill="var(--blue)"/>
</svg>
<div class="abs topbar-info">
  <span class="ico"><svg width="16" height="16" viewBox="0 0 24 24"><path d="M6.6 10.8a15 15 0 0 0 6.6 6.6l2.2-2.2c.3-.3.7-.4 1-.2 1.1.4 2.3.6 3.6.6.6 0 1 .4 1 1V20c0 .6-.4 1-1 1A17 17 0 0 1 3 4c0-.6.4-1 1-1h3.5c.6 0 1 .4 1 1 0 1.3.2 2.5.6 3.6.1.3 0 .7-.2 1z" fill="var(--blue)"/></svg></span>
  <span>01 555 0142</span>
  <span class="ico" style="margin-left:10px"><svg width="16" height="16" viewBox="0 0 24 24"><rect x="2" y="5" width="20" height="14" rx="2" fill="var(--blue)"/><path d="M3 6l9 7 9-7" stroke="#fff" stroke-width="2" fill="none"/></svg></span>
  <span>info@meridale-partners.example</span>
  <span class="soc" style="margin-left:10px"></span><span class="soc"></span><span class="soc"></span>
</div>
<div class="abs brand">
  <span class="brand-dot"></span>
  <span class="brand-name">Meridale<br>Partners</span>
</div>
<nav class="abs nav">
  <span class="active">Home</span><span>Who we are</span><span>What we do</span><span>How we do it</span><span>Contact Us</span>
</nav>

<!-- hero -->
<svg class="abs hero" width="1200" height="652" viewBox="0 0 1200 652">
  <defs>
    <linearGradient id="heroFill" x1="0" y1="0" x2="1" y2="0.4">
      <stop offset="0" stop-color="#23455a"/>
      <stop offset=".55" stop-color="#4b6a7c"/>
      <stop offset="1" stop-color="#2b3b48"/>
    </linearGradient>
  </defs>
  <path d="M0 0H1200V565Q640 720 0 485Z" fill="url(#heroFill)" role="img" aria-label="Photo of a businesswoman holding a tablet in a modern glass office"/>
  <path d="M0 500Q80 535 159 556" stroke="var(--blue)" stroke-width="11" fill="none"/>
  <path d="M181 566Q600 720 1004 572" stroke="var(--blue)" stroke-width="13" fill="none"/>
</svg>
<h1 class="abs hero-title">Welcome to<br>Meridale Partner</h1>
<p class="abs hero-text">MP are a Data Analytics &amp; EPM company, specialising in the implementation and support of Business Intelligence, EPM and Data Analytics business solutions, both in the Cloud and on-premise.</p>
<a class="abs btn btn-orange" style="left:93px;top:502px;width:167px;height:57px;font-size:18px">Get Started</a>

<!-- who we are -->
<svg class="abs" style="left:78px;top:862px" width="420" height="420" viewBox="0 0 420 420">
  <circle cx="206" cy="208" r="188" fill="#c9c3b7" role="img" aria-label="Photo of a man working on a laptop"/>
  <path d="M90 60A195 195 0 0 1 400 170" stroke="var(--blue)" stroke-width="14" fill="none"/>
  <path d="M12 250A205 205 0 0 0 360 340" stroke="var(--blue)" stroke-width="14" fill="none"/>
  <path d="M14 170L14 200" stroke="var(--blue)" stroke-width="14"/>
</svg>
<div class="abs eyebrow" style="left:599px;top:874px">About Meridale Partners</div>
<h2 class="abs h2" style="left:598px;top:900px">Who we are</h2>
<p class="abs body-text" style="left:599px;top:946px;width:490px">Meridale Partners is an exciting start-up in the Data Analytics and EPM space.</p>
<p class="abs body-text" style="left:599px;top:1033px;width:490px">Founded in 2019, MP specialise in the implementation and support of BI, EPM and Data Analytics business solutions, both in the Cloud and on-premise.MP are a Data Analytics &amp; EPM company, specialising in the implementation and support of Business Intelligence, EPM and Data Analytics business solutions, both in the Cloud and on-premise.</p>
<a class="abs btn btn-orange" style="left:600px;top:1197px;width:167px;height:60px">Read More</a>

<!-- what we do -->
<div class="abs" style="left:0;top:1348px;width:753px;height:467px;background:linear-gradient(120deg,var(--blue-dark),var(--blue))"></div>
<svg class="abs" style="left:604px;top:1382px" width="90" height="24" viewBox="0 0 90 24">
  <path d="M26 12H4M12 4L4 12l8 8" stroke="#8ea7b6" stroke-width="2.5" fill="none"/>
  <path d="M64 12h22M78 4l8 8-8 8" stroke="#fff" stroke-width="2.5" fill="none"/>
</svg>
<div class="abs eyebrow" style="left:111px;top:1437px;color:#fff">Our Services</div>
<h2 class="abs h2" style="left:111px;top:1463px;color:#fff">What we do</h2>
<p class="abs body-text" style="left:111px;top:1511px;width:290px;color:#fff">MP are a Data Analytics &amp; EPM company, specialising in the implementation and support of Business Intelligence, EPM and Data Analytics business solutions, both in the Cloud and on-premise.</p>
<a class="abs btn btn-white" style="left:111px;top:1676px;width:167px;height:60px">View More</a>

<div class="abs card" style="left:440px;top:1437px;width:363px;height:470px;background:linear-gradient(180deg,#3e4a58,#151b22)" role="img" aria-label="Photo of smiling business advisers in suits"></div>
<div class="abs card-title" style="left:467px;top:1812px">Advise &amp; Architect Services</div>
<svg class="abs" style="left:470px;top:1855px" width="26" height="20" viewBox="0 0 26 20"><path d="M2 10h20M14 2l8 8-8 8" stroke="#fff" stroke-width="2.5" fill="none"/></svg>

<div class="abs card" style="left:821px;top:1437px;width:364px;height:470px;background:linear-gradient(180deg,#8a9aa3,#2d3a3c 70%,#1b2224)" role="img" aria-label="Photo of a team collaborating around a desk with sticky notes"></div>
<div class="abs card-title" style="left:845px;top:1736px">Design &amp; Implement</div>
<p class="abs card-text" style="left:846px;top:1775px;width:322px">Working with the project management team, through each stage of the project, with clearly defined deliverables &amp; well exercised plans to deliver them.</p>
<svg class="abs" style="left:845px;top:1857px" width="26" height="20" viewBox="0 0 26 20"><path d="M2 10h20M14 2l8 8-8 8" stroke="#fff" stroke-width="2.5" fill="none"/></svg>

<!-- testimonials -->
<div class="abs eyebrow" style="left:0;width:1200px;text-align:center;top:2037px">Testimonials</div>
<h2 class="abs h2" style="left:0;width:1200px;text-align:center;top:2068px">What Customer Says</h2>
<svg class="abs" style="left:195px;top:2130px" width="340" height="330" viewBox="0 0 340 330">
  <circle cx="168" cy="167" r="143" fill="#a9b8c3" role="img" aria-label="Photo of a smiling bearded man"/>
  <path d="M95 22A158 158 0 0 1 326 178" stroke="var(--orange)" stroke-width="12" fill="none"/>
  <path d="M12 200A158 158 0 0 0 280 280" stroke="var(--orange)" stroke-width="12" fill="none"/>
  <path d="M12 130L12 160" stroke="var(--orange)" stroke-width="12"/>
</svg>
<div class="abs" style="left:64px;top:2217px;width:79px;height:79px;border-radius:50%;background:#6b6f73" role="img" aria-label="Customer portrait"></div>
<div class="abs" style="left:5px;top:2372px;width:92px;height:92px;border-radius:50%;background:#9a8c80" role="img" aria-label="Customer portrait"></div>
<svg class="abs" style="left:1030px;top:2148px" width="60" height="42" viewBox="0 0 60 42">
  <circle cx="13" cy="13" r="12" fill="var(--orange)"/><path d="M24 13Q24 34 6 40" stroke="var(--orange)" stroke-width="7" fill="none"/>
  <circle cx="43" cy="13" r="12" fill="var(--orange)"/><path d="M54 13Q54 34 36 40" stroke="var(--orange)" stroke-width="7" fill="none"/>
</svg>
<p class="abs quote" style="left:570px;top:2208px;width:520px">Temporibus autem quibusdam et aut officiis debitis aut rerum necessitbus saepe eveniet ut et voluptates repudiandae sint et molestiae non recusandae. Itaque earum rerum hic tenetur a sapiente delectus, ut aut reiciendis voluptatibus maiores alias consequatur aut perferendis doloribus asperiores repellat.</p>
<div class="abs" style="left:700px;width:388px;text-align:right;top:2370px;font-weight:700;font-size:17px">Dana Rowell, Vice President Leading</div>
<div class="abs" style="left:997px;top:2419px"><span class="dot"></span><span class="dot"></span><span class="dot" style="background:var(--blue)"></span><span class="dot"></span></div>

<!-- contact -->
<div class="abs" style="left:0;top:2521px;width:1200px;height:433px;background:linear-gradient(90deg,#e58a45,#e9995a 60%,#f0b47f)" role="img" aria-label="Softened photo of a team meeting in an office"></div>
<div class="abs eyebrow" style="left:109px;top:2609px;color:#fff">Contact Us</div>
<h2 class="abs h2" style="left:108px;top:2637px;color:#fff">Get In Touch With Us</h2>
<p class="abs body-text" style="left:109px;top:2692px;width:590px;color:#fff">Itaque earum rerum hic tenetur a sapiente delectus, ut aut reiciendis voluptatibus maiores alias consequatur aut perferendis doloribus asperiores repellat. Call us on 01 555 0142 for more information.</p>
<div class="abs" style="left:109px;top:2807px;width:405px;height:62px;border-radius:31px;background:#fff;display:flex;align-items:center;gap:18px;padding-left:8px;font-family:'Montserrat',sans-serif;font-weight:700;font-size:17px">
  <span style="width:46px;height:46px;border-radius:50%;background:var(--orange);display:inline-flex;align-items:center;justify-content:center"><svg width="18" height="14" viewBox="0 0 18 14"><rect width="18" height="14" rx="2" fill="#fff"/><path d="M1 1l8 6 8-6" stroke="var(--orange)" stroke-width="2" fill="none"/></svg></span>
  info@meridale-partners.example
</div>

<!-- footer -->
<div class="abs" style="left:0;top:2954px;width:1200px;height:451px;background:var(--footer)"></div>
<div class="abs" style="left:113px;top:3068px;display:flex;align-items:center;gap:12px">
  <span style="width:48px;height:48px;border-radius:50%;border:7px solid #fff"></span>
  <span class="brand-name" style="color:#fff;font-size:18px;line-height:21px">Meridale<br>Partners</span>
</div>
<div class="abs" style="left:113px;top:3146px"><span class="foot-soc"></span><span class="foot-soc"></span><span class="foot-soc" style="background:var(--orange)"></span><span class="foot-soc"></span></div>

<div class="abs foot-h" style="left:403px;top:3056px">Quick Link</div>
<ul class="abs foot-list" style="left:403px;top:3100px">
  <li><svg width="14" height="12" viewBox="0 0 14 12"><path d="M1 6h11M7 1l5 5-5 5" stroke="#fff" stroke-width="2" fill="none"/></svg>Home</li>
  <li><svg width="14" height="12" viewBox="0 0 14 12"><path d="M1 6h11M7 1l5 5-5 5" stroke="#fff" stroke-width="2" fill="none"/></svg>About</li>
  <li><svg width="14" height="12" viewBox="0 0 14 12"><path d="M1 6h11M7 1l5 5-5 5" stroke="#fff" stroke-width="2" fill="none"/></svg>Service</li>
  <li><svg width="14" height="12" viewBox="0 0 14 12"><path d="M1 6h11M7 1l5 5-5 5" stroke="#fff" stroke-width="2" fill="none"/></svg>FAQ</li>
  <li><svg width="14" height="12" viewBox="0 0 14 12"><path d="M1 6h11M7 1l5 5-5 5" stroke="#fff" stroke-width="2" fill="none"/></svg>Contact us</li>
</ul>

<div class="abs foot-h" style="left:626px;top:3056px">Help Link</div>
<ul class="abs foot-list" style="left:626px;top:3100px">
  <li><svg width="14" height="12" viewBox="0 0 14 12"><path d="M1 6h11M7 1l5 5-5 5" stroke="#fff" stroke-width="2" fill="none"/></svg>FAQ</li>
  <li><svg width="14" height="12" viewBox="0 0 14 12"><path d="M1 6h11M7 1l5 5-5 5" stroke="#fff" stroke-width="2" fill="none"/></svg>Terms of use</li>
  <li><svg width="14" height="12" viewBox="0 0 14 12"><path d="M1 6h11M7 1l5 5-5 5" stroke="#fff" stroke-width="2" fill="none"/></svg>Privacy Policy</li>
  <li><svg width="14" height="12" viewBox="0 0 14 12"><path d="M1 6h11M7 1l5 5-5 5" stroke="#fff" stroke-width="2" fill="none"/></svg>Support Links</li>
  <li><svg width="14" height="12" viewBox="0 0 14 12"><path d="M1 6h11M7 1l5 5-5 5" stroke="#fff" stroke-width="2" fill="none"/></svg>Conditions</li>
</ul>

<div class="abs foot-h" style="left:827px;top:3056px">Contact us</div>
<div class="abs" style="left:827px;top:3115px;display:flex;gap:14px;color:#fff;font-size:15px;line-height:27px">
  <span class="foot-soc" style="margin:6px 0 0;display:inline-flex;align-items:center;justify-content:center;flex:none"><svg width="12" height="16" viewBox="0 0 12 16"><path d="M6 0a6 6 0 0 1 6 6c0 4-6 10-6 10S0 10 0 6a6 6 0 0 1 6-6z" fill="#fff"/><circle cx="6" cy="6" r="2.2" fill="var(--blue)"/></svg></span>
  <span>14 Harbour Lane, Northgate,<br>Dublin 4, D04 AB12</span>
</div>
<div class="abs" style="left:827px;top:3194px;display:flex;align-items:center;gap:14px;color:#fff;font-size:15px">
  <span class="foot-soc" style="margin:0;display:inline-flex;align-items:center;justify-content:center"><svg width="14" height="14" viewBox="0 0 24 24"><path d="M6.6 10.8a15 15 0 0 0 6.6 6.6l2.2-2.2c.3-.3.7-.4 1-.2 1.1.4 2.3.6 3.6.6.6 0 1 .4 1 1V20c0 .6-.4 1-1 1A17 17 0 0 1 3 4c0-.6.4-1 1-1h3.5c.6 0 1 .4 1 1 0 1.3.2 2.5.6 3.6.1.3 0 .7-.2 1z" fill="#fff"/></svg></span>
  01 555 0142
</div>
<div class="abs" style="left:827px;top:3245px;display:flex;align-items:center;gap:14px;color:#fff;font-size:14px">
  <span class="foot-soc" style="margin:0;display:inline-flex;align-items:center;justify-content:center"><svg width="14" height="11" viewBox="0 0 18 14"><rect width="18" height="14" rx="2" fill="#fff"/><path d="M1 1l8 6 8-6" stroke="var(--blue)" stroke-width="2" fill="none"/></svg></span>
  info@meridale-partners.example
</div>

<div class="abs" style="left:111px;top:3311px;width:978px;height:1px;background:#555"></div>
<div class="abs" style="left:0;width:1200px;text-align:center;top:3348px;color:#fff;font-weight:700;font-size:15px">Copyrights@2022.Meridale Partners.All Rights Reserved</div>

</body>
</html>
```